Health Care Company with Logo Needs Business Cards designed

We are a luxury behavioral health company looking for business cards design we already have a logo and are looking for someone to design a sophisticated luxurious looking business card. Please note that Card design should be captivating just like the logo and also encompass the logo color

Industry/Entity Type

Healthcare

Contact Information for Business Card

Logo,company name, tagline, my name and title, contact details, and physical address

```html
<!DOCTYPE html>
<html lang="en">
<head>
<meta charset="utf-8">
<title>Orren Behavioral Health – Business Cards</title>
<link href="https://fonts.googleapis.com/css2?family=Roboto+Condensed:wght@500&family=Roboto:ital,wght@0,400;0,500;1,400&display=swap" rel="stylesheet">
<style>
  :root {
    --backdrop: #2a2a2b;
    --card: #1f1f21;
    --card-edge: #262628;
    --purple: #7a3a93;
    --blue: #1e9bd7;
    --orange: #f39314;
    --green: #8cc63f;
    --text: #e6e6e6;
    --muted: #d2d2d2;
  }
  * { margin: 0; padding: 0; box-sizing: border-box; }
  html, body { width: 1138px; height: 1200px; overflow: hidden; }
  body {
    background: var(--backdrop);
    position: relative;
    font-family: "Roboto", Arial, sans-serif;
  }
  .card {
    position: absolute;
    border-radius: 16px;
    background: linear-gradient(160deg, var(--card-edge), var(--card));
    overflow: hidden;
    box-shadow: 0 6px 18px rgba(0,0,0,.35);
  }
  .card--back { left: 186px; top: 302px; width: 376px; height: 624px; }
  .card--front { left: 608px; top: 305px; width: 374px; height: 619px; text-align: center; }

  .pattern-field {
    position: absolute; left: 0; top: 0; width: 100%; height: 520px;
    background:
      radial-gradient(ellipse at 40% 15%, rgba(150,150,155,.35), transparent 60%),
      linear-gradient(180deg, #3c3c3e 0%, #2c2c2e 45%, #151516 100%);
  }
  .brand-mark {
    border-radius: 50%;
    background: var(--orange);
  }
  .card--back .brand-mark {
    position: absolute; left: 129px; top: 410px; width: 102px; height: 102px;
  }
  .brand-name {
    font-family: "Roboto Condensed", "Arial Narrow", sans-serif;
    font-weight: 500;
    color: var(--purple);
    white-space: nowrap;
  }
  .tagline {
    font-family: "Roboto", Arial, sans-serif;
    font-weight: 500;
    color: var(--blue);
    text-transform: uppercase;
    white-space: nowrap;
  }
  .card--back .brand-name { position: absolute; left: 29px; top: 534px; font-size: 33px; line-height: 1; }
  .card--back .tagline { position: absolute; left: 30px; top: 574px; font-size: 9.5px; letter-spacing: 2.6px; }

  .card--front .brand-mark { width: 124px; height: 124px; margin: 66px auto 0; }
  .card--front .brand-name { margin-top: 26px; font-size: 29px; line-height: 1; }
  .card--front .tagline { margin-top: 8px; font-size: 8.5px; letter-spacing: 2.3px; }

  .person-name { margin-top: 68px; font-size: 22px; font-weight: 500; color: var(--blue); letter-spacing: .5px; }
  .person-title { margin-top: 4px; font-size: 15px; font-style: italic; color: var(--muted); }

  .divider { margin: 30px auto 0; display: flex; align-items: center; justify-content: center; gap: 6px; }
  .divider__line { width: 56px; height: 2px; }
  .divider__line--left { background: linear-gradient(90deg, transparent, var(--purple)); margin-right: 10px; }
  .divider__line--right { background: linear-gradient(90deg, var(--blue), transparent); margin-left: 10px; }
  .divider svg { display: block; }

  .contact { margin-top: 16px; font-size: 14.5px; line-height: 22px; color: var(--text); }
  .address { margin-top: 18px; font-size: 14.5px; line-height: 22px; color: var(--text); }
</style>
</head>
<body>

  <section class="card card--back">
    <div class="pattern-field" role="img" aria-label="Repeating embossed brand monogram pattern in glossy black tones"></div>
    <div class="brand-mark" aria-hidden="true"></div>
    <p class="brand-name">Orren Behavioral Health</p>
    <p class="tagline">Dedicated to hope, healing and recovery</p>
  </section>

  <section class="card card--front">
    <div class="brand-mark" aria-hidden="true"></div>
    <p class="brand-name">Orren Behavioral Health</p>
    <p class="tagline">Dedicated to hope, healing and recovery</p>

    <p class="person-name">DANIEL ORREN</p>
    <p class="person-title">Managing Director</p>

    <div class="divider">
      <span class="divider__line divider__line--left"></span>
      <svg width="22" height="22" viewBox="0 0 22 22" aria-label="Phone">
        <circle cx="11" cy="11" r="10" fill="none" stroke="var(--purple)" stroke-width="1.6"/>
        <path d="M7 8c0 4 3 7 7 7l1.2-1.6-2-1.2-1 1c-1.4-.6-2.4-1.6-3-3l1-1-1.2-2z" fill="var(--blue)"/>
      </svg>
      <svg width="22" height="22" viewBox="0 0 22 22" aria-label="Email">
        <circle cx="11" cy="11" r="10" fill="none" stroke="var(--purple)" stroke-width="1.6"/>
        <rect x="6" y="7.5" width="10" height="7" fill="none" stroke="var(--blue)" stroke-width="1.3"/>
        <path d="M6 7.5l5 4 5-4" fill="none" stroke="var(--blue)" stroke-width="1.3"/>
      </svg>
      <svg width="22" height="22" viewBox="0 0 22 22" aria-label="Website">
        <circle cx="11" cy="11" r="10" fill="none" stroke="var(--purple)" stroke-width="1.6"/>
        <circle cx="11" cy="11" r="5.5" fill="none" stroke="var(--blue)" stroke-width="1.2"/>
        <ellipse cx="11" cy="11" rx="2.4" ry="5.5" fill="none" stroke="var(--blue)" stroke-width="1"/>
        <path d="M5.5 11h11" stroke="var(--blue)" stroke-width="1"/>
      </svg>
      <span class="divider__line divider__line--right"></span>
    </div>

    <p class="contact">000-111-0000<br>hello@orrenbehavioral.com<br>www.orrenbehavioral.com</p>
    <p class="address">123, Anywhere ST, Any City,<br>Any Town, US 123456</p>
  </section>

</body>
</html>
```